Fizz's Shed & Grill Burger Restaurant Website - HomePage Only PSD

I need a website design for a restaurant called "Fizz's Shed and Grill" featuring burgers, wings, beer, live music, trivia, and more. I have several images of the restaurant and they already have their logo files created (see attached). I want some type of wood background and integrate the silver tin. This needs to be a modern, hip and fun type design. Design must incorporate these attached graphics.

UPDATE - just added a few more images of things I really like to be incorporated into my designs.
Updates

Industry/Entity Type

Burger Restaurant

Number of Pages Required

1 page

Font styles to use
Sans Serif

Requirements
Must have
• Restaurant/Bar theme with integration of existing logo and the red wood look.
Nice to have
• - Modern Fun appearance
• - Use Pelko Fonts

```html
<!DOCTYPE html>
<html lang="en">
<head>
<meta charset="utf-8">
<title>Fizz's Shed and Grill</title>
<link href="https://fonts.googleapis.com/css2?family=Lato:wght@400;700;900&family=Montserrat:wght@400&display=swap" rel="stylesheet">
<style>
:root{
  --red:#a5090f;
  --red-dark:#5e0306;
  --red-mid:#8a050a;
  --wood-a:#7a0509;
  --wood-b:#b3121a;
  --text:#222;
  --muted:#444;
  --light:#f1f1f1;
  --line:#c9c9c9;
  --white:#fff;
  --tin-a:#d7d7d7;
  --tin-b:#a9a9a9;
  --cap:rgba(70,70,70,.85);
}
*{box-sizing:border-box;margin:0;padding:0}
html,body{width:726px;height:1200px;overflow:hidden}
body{position:relative;font-family:"Lato",sans-serif;color:var(--text);background:var(--white)}
.abs{position:absolute}
.wood{background:
  repeating-linear-gradient(90deg,rgba(0,0,0,.08) 0 3px,transparent 3px 17px,rgba(255,255,255,.04) 17px 19px,transparent 19px 41px),
  linear-gradient(90deg,var(--wood-a),var(--wood-b) 35%,var(--red-mid) 60%,var(--wood-b) 85%,var(--wood-a))}

/* header */
.site-header{left:0;top:0;width:726px;height:88px}
.brand{left:48px;top:22px;display:flex;align-items:center;gap:6px;color:var(--white);font-weight:900;font-size:12px}
.brand-dot{width:44px;height:44px;border:2px solid var(--white);border-radius:50%}
.book-btn{left:466px;top:13px;height:20px;display:flex;font-size:8.5px;font-weight:700}
.book-btn span{background:#eee;color:var(--red);padding:0 6px;line-height:20px;border-radius:3px 0 0 3px}
.book-btn b{background:#222;width:22px;border-radius:0 3px 3px 0;display:flex;align-items:center;justify-content:center}
.phone{left:574px;top:15px;color:var(--white);font-size:13px;font-weight:700;display:flex;align-items:center;gap:6px;letter-spacing:.3px}
.main-nav{left:282px;top:54px;display:flex;align-items:center;color:var(--white);font-weight:700;font-size:11px}
.main-nav a{padding:0 11px;border-left:1px solid rgba(255,255,255,.35);line-height:12px}
.main-nav a:first-child{border:none;padding-left:0}

/* hero */
.hero{left:0;top:88px;width:726px;height:256px;
  background:radial-gradient(ellipse at 62% 45%,#f6b13a 0,#d57c10 30%,transparent 60%),
  linear-gradient(90deg,#3a1a06 0,#8a4a10 30%,#c97a16 60%,#6f3a0c 100%)}
.hero h1{left:48px;top:100px;color:var(--white);font-size:30px;font-weight:700}
.hero p{left:48px;top:145px;width:300px;color:var(--white);font-size:11.3px;font-weight:700;line-height:14px}
.dots{left:336px;top:238px;width:58px;height:18px;background:var(--white);border-radius:14px 14px 0 0;display:flex;gap:5px;justify-content:center;padding-top:6px}
.dots i{width:5px;height:5px;border-radius:50%;background:#ccc}
.dots i:first-child{background:var(--red)}

/* features */
.features{left:0;top:344px;width:726px;height:192px}
.feature{width:146px;top:26px}
.feature h3{display:flex;align-items:center;gap:6px;color:var(--white);font-size:12px;font-weight:700;height:28px}
.mini-dot{width:24px;height:24px;border:1.5px solid var(--white);border-radius:50%}
.feature .photo{height:64px;margin-top:5px}
.feature .cap{height:37px;background:var(--cap);color:#eee;font-size:7.2px;line-height:11px;padding:3px 6px;position:relative}
.feature .cap::after{content:"+";position:absolute;right:0;bottom:0;width:16px;height:16px;background:#111;clip-path:polygon(100% 0,100% 100%,0 100%);color:var(--white);font-size:10px;font-weight:900;text-align:right;padding-right:2px;line-height:18px}
.arrow{color:var(--white);font-size:16px;font-weight:900}

/* about */
.about{left:0;top:536px;width:726px;height:219px;background:var(--light)}
.sec-title{display:flex;align-items:center;gap:6px;font-family:"Montserrat",sans-serif;font-size:18px;color:#111;border-bottom:1px solid var(--line);padding-bottom:4px}
.sec-title em{font-style:normal;color:var(--red)}
.sec-dot{width:26px;height:26px;border:1.5px solid #333;border-radius:50%}
.about-title{left:49px;top:24px;width:390px}
.about-text{left:53px;top:62px;width:390px;font-size:9.9px;line-height:14.5px;color:var(--text)}
.checks{left:53px;top:125px;list-style:none;font-size:8.2px;color:var(--text)}
.checks li{display:flex;align-items:center;gap:6px;height:18.5px}
.book-title{left:470px;top:24px;width:195px}
.form{left:473px;top:66px;width:192px}
.field{height:20px;border:1px solid var(--line);background:var(--white);font-size:7.5px;padding-left:8px;line-height:18px;margin-bottom:8.6px;position:relative;color:#222}
.submit{display:flex;height:15px;font-size:10px;font-weight:700;margin-top:4px}
.submit span{background:var(--red);color:var(--white);padding:0 5px;line-height:15px;border-radius:2px 0 0 2px}
.submit b{background:#222;width:17px;border-radius:0 2px 2px 0;display:flex;align-items:center;justify-content:center}

/* gallery */
.gallery{left:0;top:755px;width:726px;height:300px}
.gallery-tab{left:278px;top:0;width:170px;height:27px;background:#e3e3e3;border-radius:0 0 10px 10px;text-align:center;font-family:"Montserrat",sans-serif;font-size:17px;line-height:27px}
.gallery-tab em{font-style:normal;color:var(--red)}
.shot{width:108px;height:108px;border-radius:50%;top:65px;box-shadow:0 3px 6px rgba(0,0,0,.4);overflow:hidden}
.shot .over{position:absolute;inset:0;background:rgba(40,20,10,.55);color:var(--white);font-size:8px;font-weight:700;text-align:center;padding:38px 10px 0;line-height:11px}

/* footer */
.footer-tin{left:0;top:0;width:726px;height:1200px;pointer-events:none}
.footer-badge{left:330px;top:956px;width:60px;height:60px;border-radius:50%;background:var(--white);border:2px solid var(--red);display:flex;align-items:center;justify-content:center;text-align:center;color:var(--red);font-weight:900;font-size:7.5px;line-height:9px}
.foot-h{color:var(--red);font-size:11px;font-weight:700;border-bottom:1px dotted #888;padding-bottom:5px}
.quick{left:50px;top:1041px;width:75px}
.quick ul{list-style:none;margin-top:6px;font-size:8px;color:#222}
.quick li{height:14.5px;display:flex;align-items:center;gap:6px}
.quick li::before{content:"›";color:var(--red);font-weight:700}
.contact{left:236px;top:1041px;width:116px}
.contact .row{display:flex;gap:8px;font-size:8px;line-height:12px;margin-top:10px;color:#222}
.map{left:376px;top:1038px;width:92px;height:118px}
.big-mark{left:577px;top:1032px;width:100px;height:100px;border-radius:50%;border:3px solid #333;display:flex;align-items:center;justify-content:center;text-align:center;font-weight:900;font-size:11px;line-height:14px;color:#333}
.social{left:572px;top:1138px;display:flex;gap:5px}
.social i{width:20px;height:20px;border-radius:50%;background:var(--red);display:block}
.copyright{left:0;top:1174px;width:726px;height:26px;background:var(--red);color:var(--white);font-size:8px;font-weight:700;text-align:center;line-height:26px}
.divider{width:1px;background:rgba(255,255,255,.5);top:1040px;height:110px}
</style>
</head>
<body>

<header class="site-header wood abs">
  <div class="brand abs"><span class="brand-dot"></span>Fizz's Shed<br>&amp; Grill</div>
  <div class="book-btn abs"><span>Book A Table</span><b><svg width="10" height="8" viewBox="0 0 10 8"><path d="M1 1l3 3-3 3M5 1l3 3-3 3" stroke="#fff" fill="none" stroke-width="1.3"/></svg></b></div>
  <div class="phone abs"><svg width="12" height="12" viewBox="0 0 24 24"><path fill="#ccc" d="M6.6 10.8a15 15 0 0 0 6.6 6.6l2.2-2.2c.3-.3.7-.4 1-.2 1.1.4 2.3.6 3.6.6.6 0 1 .4 1 1V20c0 .6-.4 1-1 1A17 17 0 0 1 3 4c0-.6.4-1 1-1h3.5c.6 0 1 .4 1 1 0 1.3.2 2.5.6 3.6.1.3 0 .7-.2 1z"/></svg>555-014-2286</div>
  <nav class="main-nav abs">
    <a><svg width="16" height="14" viewBox="0 0 16 14"><path d="M8 1L1 7h2v6h4V9h2v4h4V7h2z" fill="#fff"/></svg></a>
    <a>About Us</a><a>Our Menus</a><a>Gallery</a><a>Reservations</a><a>Contact Us</a>
  </nav>
</header>

<section class="hero abs" role="img" aria-label="Two glasses of golden beer with foam on a warm amber background">
  <h1 class="abs">A Simple Beer</h1>
  <p class="abs">Lorem ipsum dolor sit amet, consectetur adipiscing elit. Integer vitae interdum mi. Donec ac sollicitudin velit, ac sodales nibh. Aliquam congue diam vel magna</p>
  <div class="dots abs"><i></i><i></i><i></i><i></i></div>
</section>

<section class="features wood abs">
  <span class="arrow abs" style="left:15px;top:84px">‹</span>
  <span class="arrow abs" style="left:702px;top:84px">›</span>
  <div class="feature abs" style="left:49px">
    <h3><span class="mini-dot"></span>Burgers</h3>
    <div class="photo" role="img" aria-label="Cheeseburger with lettuce" style="background:linear-gradient(180deg,#e8e2d8,#c58a45 45%,#5c3a1e 70%,#5f8a2c)"></div>
    <div class="cap">Lorem ipsum dolor sit amet, in the adipiscing magnagt Lorem ipsum dolor magnagt...</div>
  </div>
  <div class="feature abs" style="left:210px">
    <h3><span class="mini-dot"></span>Wings</h3>
    <div class="photo" role="img" aria-label="Plate of glazed chicken wings" style="background:linear-gradient(135deg,#f2e9e0,#c8621e 40%,#8e3410 75%,#e6d6c4)"></div>
    <div class="cap">Lorem ipsum dolor sit amet, in the adipiscing magnagt Lorem ipsum dolor magnagt...</div>
  </div>
  <div class="feature abs" style="left:368px">
    <h3><span class="mini-dot"></span>Beer</h3>
    <div class="photo" role="img" aria-label="Mugs of beer on a dark bar" style="background:radial-gradient(ellipse at 65% 65%,#e7a326,#8a4a0c 40%,#1a0a04 75%)"></div>
    <div class="cap">Lorem ipsum dolor sit amet, in the adipiscing magnagt Lorem ipsum dolor magnagt...</div>
  </div>
  <div class="feature abs" style="left:530px">
    <h3><span class="mini-dot"></span>Live Music</h3>
    <div class="photo" role="img" aria-label="Concert crowd with raised hands under stage lights" style="background:linear-gradient(180deg,#f0b8d2,#c04a86 45%,#4a1030)"></div>
    <div class="cap">Lorem ipsum dolor sit amet, in the adipiscing magnagt Lorem ipsum dolor magnagt...</div>
  </div>
</section>

<section class="about abs">
  <h2 class="sec-title about-title abs"><span class="sec-dot"></span>About&nbsp;<em>Fizz's Shed and Grill</em></h2>
  <p class="about-text abs">Lorem ipsum dolor sit amet, consectetuer adipiscing elit, sed diam nonummy nibh euismod tincidunt ut laoreet dolore magna aliquam erat volutpat. Ut wisi enim ad minim veniam, quis nostrud exerci tation ullamcorper suscipit lobortis nisl ut aliquip ex ea commodo consequat.</p>
  <ul class="checks abs">
    <li><svg width="9" height="8" viewBox="0 0 9 8"><path d="M1 4l2.5 3L8 1" stroke="#a5090f" stroke-width="1.8" fill="none"/></svg>Lorem ipsum dolor sit amet, consectetuer adipiscing elit</li>
    <li><svg width="9" height="8" viewBox="0 0 9 8"><path d="M1 4l2.5 3L8 1" stroke="#a5090f" stroke-width="1.8" fill="none"/></svg>Lorem ipsum dolor sit amet consectetuer</li>
    <li><svg width="9" height="8" viewBox="0 0 9 8"><path d="M1 4l2.5 3L8 1" stroke="#a5090f" stroke-width="1.8" fill="none"/></svg>Lorem ipsum dolor sit amet consectetuer adipiscing</li>
    <li><svg width="9" height="8" viewBox="0 0 9 8"><path d="M1 4l2.5 3L8 1" stroke="#a5090f" stroke-width="1.8" fill="none"/></svg>Lorem ipsum dolor sit amet consectetuer adipiscing</li>
  </ul>

  <h2 class="sec-title book-title abs"><span class="sec-dot"></span>Book&nbsp;<em>A Table</em></h2>
  <form class="form abs">
    <div class="field">Name :</div>
    <div class="field">Email :</div>
    <div class="field">Phone :</div>
    <div class="field">Number of Persons<svg class="abs" style="right:8px;top:6px" width="8" height="6" viewBox="0 0 8 6"><path d="M1 1l3 3 3-3" stroke="#333" fill="none"/></svg></div>
    <div class="submit"><span>Submit</span><b><svg width="9" height="7" viewBox="0 0 10 8"><path d="M1 1l3 3-3 3M5 1l3 3-3 3" stroke="#fff" fill="none" stroke-width="1.3"/></svg></b></div>
  </form>
</section>

<section class="gallery wood abs">
  <div class="gallery-tab abs">Project <em>Gallery</em></div>
  <span class="arrow abs" style="left:14px;top:110px">‹</span>
  <span class="arrow abs" style="left:702px;top:110px">›</span>
  <div class="shot abs" style="left:48px" role="img" aria-label="Burger close-up" style2=""><div style="width:100%;height:100%;background:linear-gradient(180deg,#f2f2f2,#d08a3a 30%,#4a2a14 60%,#e6b020 70%,#c6823c)"></div></div>
  <div class="shot abs" style="left:178px" role="img" aria-label="Painted cow statue outside the restaurant"><div style="width:100%;height:100%;background:linear-gradient(180deg,#5d9fd8,#a9c9e6 45%,#6a8ac0 60%,#8a8a5a)"></div></div>
  <div class="shot abs" style="left:308px" role="img" aria-label="Restaurant entrance with red roof"><div style="width:100%;height:100%;background:linear-gradient(180deg,#9a2a22,#4a3a30 40%,#3a2e26)"></div><div class="over">Lorem ipsum dolor sit amet, consectetuer adipiscing sed diam</div></div>
  <div class="shot abs" style="left:437px" role="img" aria-label="Wooden patio fence under blue sky"><div style="width:100%;height:100%;background:linear-gradient(180deg,#6aa8e0,#cfe2f2 35%,#8a5a3a 55%,#d8d0c0)"></div></div>
  <div class="shot abs" style="left:568px" role="img" aria-label="Restaurant sign on wooden facade"><div style="width:100%;height:100%;background:linear-gradient(180deg,#5aa0e0,#b0502a 40%,#8a3a1e)"></div></div>
</section>

<svg class="footer-tin abs" viewBox="0 0 726 1200" aria-hidden="true">
  <defs>
    <linearGradient id="tin" x1="0" y1="0" x2="0" y2="1">
      <stop offset="0" stop-color="#d9d9d9"/><stop offset="1" stop-color="#a8a8a8"/>
    </linearGradient>
    <pattern id="ridges" width="4" height="4" patternUnits="userSpaceOnUse"><rect width="4" height="2" fill="rgba(255,255,255,.12)"/></pattern>
  </defs>
  <path d="M0 1036 Q363 950 726 1036 V1174 H0Z" fill="#7a0509"/>
  <path d="M0 1040 Q363 958 726 1040 V1174 H0Z" fill="url(#tin)"/>
  <path d="M0 1040 Q363 958 726 1040 V1174 H0Z" fill="url(#ridges)"/>
  <path d="M0 1040 Q363 958 726 1040" stroke="#a5090f" stroke-width="2" fill="none"/>
</svg>
<div class="divider abs" style="left:182px"></div>
<div class="divider abs" style="left:524px"></div>

<div class="footer-badge abs">Fizz's<br>Shed &amp;<br>Grill</div>

<div class="quick abs">
  <div class="foot-h">Quick Links</div>
  <ul><li>Home</li><li>About Us</li><li>Our Menus</li><li>Gallery</li><li>Reservations</li><li>Contact Us</li></ul>
</div>

<div class="contact abs">
  <div class="foot-h">Contact Details</div>
  <div class="row"><svg width="8" height="10" viewBox="0 0 8 10"><path d="M4 0a4 4 0 0 0-4 4c0 3 4 6 4 6s4-3 4-6a4 4 0 0 0-4-4z" fill="#a5090f"/><circle cx="4" cy="4" r="1.4" fill="#ccc"/></svg><span>14 Harbor Mill Road<br>Lindale, MS</span></div>
  <div class="row" style="margin-top:13px"><svg width="9" height="9" viewBox="0 0 10 10"><circle cx="5" cy="5" r="4" stroke="#a5090f" stroke-width="1.3" fill="none"/><path d="M5 2.5V5h2" stroke="#a5090f" fill="none"/></svg><span>Mon-Sat : 10-2300<br>Sun : 11-2200</span></div>
  <div class="row" style="margin-top:12px;font-weight:700"><svg width="9" height="9" viewBox="0 0 24 24"><path fill="#a5090f" d="M6.6 10.8a15 15 0 0 0 6.6 6.6l2.2-2.2c.3-.3.7-.4 1-.2 1.1.4 2.3.6 3.6.6.6 0 1 .4 1 1V20c0 .6-.4 1-1 1A17 17 0 0 1 3 4c0-.6.4-1 1-1h3.5c.6 0 1 .4 1 1 0 1.3.2 2.5.6 3.6.1.3 0 .7-.2 1z"/></svg><span>(01) 555 0142</span></div>
</div>

<svg class="map abs" viewBox="0 0 92 118" role="img" aria-label="Location map of the restaurant">
  <path d="M46 118 C20 80 0 62 4 36 C8 12 26 0 46 0 C70 0 90 14 90 40 C90 66 70 84 46 118Z" fill="#e8e6e0" stroke="#fff" stroke-width="2"/>
</svg>

<div class="big-mark abs">Fizz's<br>Shed &amp; Grill</div>
<div class="social abs"><i></i><i></i><i></i><i></i></div>

<footer class="copyright abs">Copyright © 2015 Fizz's Shed and Grill. All Rights Reserved.</footer>

</body>
</html>
```